Medical centre needs a business card

We are a medcial centre in Australia, needing a new business card. Our demographic is low working class families. We are going to be renovating our premises to modernise the look and also had a new logo done a few months ago representing quality and community, and now need to update our cards. It needs to be doubled sided, with logo and contact details on the front, and appointment details on the back. . Needs to be modern and simple, easy to read. <br/><br/>Name: Kindle Grove Medical Centre <br/>Address: 512 Parmley Rd (Cnr Parmley Rd & Osgood Creek Rd),<br/>Tindarra Court Shopping Centre, Ashvale, SA 5199<br/>Ph: 08 8461 3072<br/>Tag line: Where your wellbeing comes first<br/>Website: www.kindlegrovemedicalcentre-example.com.au<br/>Online bookings also available<br/><br/>(On the back, to have 3 lines of appointments that can be written in.<br/>Day, date, time)<br/><br/>Your next appointment is on<br/>Can try “M T W Th F Sa Su _________________ at ____________ am/pm” or other combinations <br/>Please advise as soon as possible if unable to attend<br/>Cancellation fees apply if less than 2 hrs notice<br/>Online appointments available (please highlight this option by either by position, colour or font)

Target Market(s)

Lower social economic working class, young families to seniors

Industry/Entity Type

Medical Centre

Contact Information for Business Card

Kindle Grove Medical Centre
512 Parmley Rd (Cnr Parmley Rd & Osgood Creek Drive)
Tindarra Court Shopping Centre
Paralowie SA 5108
Ph: 08 8461 3072
www.kindlegrovemedicalcentre-example.com.au
Tagline line: where your wellbeing comes first
Back side is for appointments
Your next appointment is with Dr ______________
Day/date/time (Please give 3 lines of appointments)
Please advise as soon as possible if unable to attend
Cancellation fees apply if less than 2 hours notice
Online appointments available
Book online easily and conveniently (please highlight online appointments)

Font styles to use
Serif
Sans Serif

Colors

Designer to choose colors to be used in the design.

Requirements
Must have
• Modern and simple
• Easy to ready
• Induces a wellbeing feeling
• Incorporate our logo colours and feel from logo
• Induces feeling of stability and security
Nice to have
• Attract attention
• Pleasant to look at
• Feeling of innovation
Should not have
• Loud clashing colours
• Overly luxurious feeling
• Overly artistic

```html
<!DOCTYPE html>
<html lang="en">
<head>
<meta charset="utf-8">
<title>Kindle Grove Medical Centre – Business Card</title>
<link rel="stylesheet" href="https://fonts.googleapis.com/css2?family=PT+Sans:wght@400;700&family=PT+Sans+Narrow:wght@400;700&display=swap">
<style>
  :root {
    --bg: #2e2a3a;
    --ink: #0d5fc0;
    --ink-dark: #0a4fa3;
    --card-top: #eefaff;
    --card-bottom: #bfeefc;
    --tile: rgba(150, 215, 245, 0.35);
    --line: rgba(120, 200, 235, 0.45);
    --pill: #0d5fc0;
    --white: #ffffff;
  }
  * { box-sizing: border-box; margin: 0; padding: 0; }
  html, body { width: 1200px; height: 800px; overflow: hidden; }
  body {
    background: var(--bg);
    font-family: "PT Sans", sans-serif;
    color: var(--ink);
    display: flex;
    align-items: center;
    justify-content: center;
    gap: 32px;
  }
  .card {
    position: relative;
    width: 560px;
    height: 322px;
    border-radius: 6px;
    overflow: hidden;
    background: linear-gradient(150deg, var(--card-top) 0%, #d9f5ff 45%, var(--card-bottom) 100%);
    box-shadow: 0 18px 40px rgba(0,0,0,0.45);
  }
  .card-grid { position: absolute; inset: 0; }
  .card-content { position: relative; height: 100%; }

  /* Appointment side */
  .appointment { padding: 26px 30px; font-family: "PT Sans Narrow", sans-serif; }
  .appointment-doctor { font-size: 19px; font-weight: 700; display: flex; align-items: flex-end; }
  .fill-line { flex: 1; border-bottom: 1.5px solid var(--ink); margin-left: 6px; height: 1px; margin-bottom: 4px; }
  .day-options { display: flex; justify-content: space-between; margin: 12px 0 10px; font-size: 18px; font-weight: 700; }
  .day-options span::before {
    content: ""; display: inline-block; width: 11px; height: 11px;
    border: 1.5px solid var(--ink); margin-right: 5px; vertical-align: 0;
  }
  .slot { display: flex; align-items: flex-end; font-size: 18px; font-weight: 700; margin-bottom: 9px; }
  .slot-dot { width: 11px; height: 11px; border-radius: 50%; background: var(--ink); margin-right: 7px; margin-bottom: 6px; }
  .slot .fill-line { margin-right: 8px; }
  .notice { font-size: 16.5px; font-weight: 700; line-height: 1.3; margin-top: 8px; }
  .online-pill {
    display: inline-block; margin-top: 10px;
    background: var(--pill); color: var(--white);
    font-size: 14px; font-weight: 700; letter-spacing: 1px;
    padding: 5px 22px; border-radius: 14px;
  }

  /* Identity side */
  .identity { padding: 40px 30px 26px; }
  .brand { display: flex; flex-direction: column; align-items: flex-start; margin-left: 40px; }
  .brand-name-row { display: flex; align-items: center; gap: 12px; }
  .brand-mark { width: 34px; height: 34px; background: var(--ink); border-radius: 3px; flex: none; }
  .brand-name { font-size: 27px; font-weight: 700; letter-spacing: 0.5px; line-height: 1.05; color: var(--ink); }
  .tagline { font-size: 14px; letter-spacing: 2px; margin-top: 8px; color: var(--ink-dark); }
  .contact {
    position: absolute; right: 30px; bottom: 26px;
    list-style: none; text-align: right; font-family: "PT Sans Narrow", sans-serif;
  }
  .contact li { display: flex; align-items: center; justify-content: flex-end; gap: 10px; margin-top: 5px; font-size: 14px; font-weight: 700; line-height: 1.2; }
  .contact .phone { font-size: 22px; }
  .contact svg { width: 18px; height: 18px; flex: none; }
</style>
</head>
<body>

  <section class="card card-back">
    <svg class="card-grid" viewBox="0 0 560 322" aria-hidden="true">
      <g fill="none" stroke="var(--line)" stroke-width="1">
        <line x1="140" y1="0" x2="140" y2="322"/><line x1="280" y1="0" x2="280" y2="322"/><line x1="420" y1="0" x2="420" y2="322"/>
        <line x1="0" y1="107" x2="560" y2="107"/><line x1="0" y1="214" x2="560" y2="214"/>
      </g>
      <rect x="0" y="120" width="70" height="70" fill="var(--tile)"/>
      <rect x="470" y="240" width="90" height="82" fill="var(--tile)"/>
      <rect x="300" y="20" width="50" height="50" fill="var(--tile)"/>
    </svg>
    <div class="card-content appointment">
      <p class="appointment-doctor">Your next appointment is with: Dr.<span class="fill-line"></span></p>
      <div class="day-options"><span>Mon</span><span>Tue</span><span>Wed</span><span>Thu</span><span>Fri</span><span>Sat</span><span>Sun</span></div>
      <p class="slot"><span class="slot-dot"></span>Date:<span class="fill-line"></span>Time:<span class="fill-line"></span>am/pm</p>
      <p class="slot"><span class="slot-dot"></span>Date:<span class="fill-line"></span>Time:<span class="fill-line"></span>am/pm</p>
      <p class="slot"><span class="slot-dot"></span>Date:<span class="fill-line"></span>Time:<span class="fill-line"></span>am/pm</p>
      <p class="notice">Please advise as soon as possible if unable to attend<br>Cancellation fees apply if less than 2 hours notice</p>
      <span class="online-pill">ONLINE APPOINTMENTS AVAILABLE</span>
    </div>
  </section>

  <section class="card card-front">
    <svg class="card-grid" viewBox="0 0 560 322" aria-hidden="true">
      <g fill="none" stroke="var(--line)" stroke-width="1">
        <line x1="140" y1="0" x2="140" y2="322"/><line x1="280" y1="0" x2="280" y2="322"/><line x1="420" y1="0" x2="420" y2="322"/>
        <line x1="0" y1="107" x2="560" y2="107"/><line x1="0" y1="214" x2="560" y2="214"/>
      </g>
      <rect x="490" y="40" width="70" height="70" fill="var(--tile)"/>
      <rect x="440" y="120" width="60" height="60" fill="var(--tile)"/>
      <rect x="60" y="190" width="80" height="80" fill="var(--tile)"/>
    </svg>
    <div class="card-content identity">
      <div class="brand">
        <div class="brand-name-row">
          <span class="brand-mark"></span>
          <span class="brand-name">KINDLE GROVE<br>MEDICAL CENTRE</span>
        </div>
        <p class="tagline">Where your wellbeing comes first</p>
      </div>
      <ul class="contact">
        <li class="phone">08 8461 3072
          <svg viewBox="0 0 24 24"><path fill="var(--ink)" d="M6.6 10.8a15 15 0 0 0 6.6 6.6l2.2-2.2a1 1 0 0 1 1-.25 11.4 11.4 0 0 0 3.6.57 1 1 0 0 1 1 1V20a1 1 0 0 1-1 1A17 17 0 0 1 3 4a1 1 0 0 1 1-1h3.5a1 1 0 0 1 1 1c0 1.25.2 2.45.57 3.57a1 1 0 0 1-.25 1z"/></svg></li>
        <li>hello@kindlegrove-example.com.au
          <svg viewBox="0 0 24 24"><rect x="3" y="5" width="18" height="14" rx="1.5" fill="none" stroke="var(--ink)" stroke-width="2"/><path d="M3 6l9 7 9-7" fill="none" stroke="var(--ink)" stroke-width="2"/></svg></li>
        <li>www.kindlegrovemedicalcentre-example.com.au
          <svg viewBox="0 0 24 24"><g fill="none" stroke="var(--ink)" stroke-width="1.8"><circle cx="12" cy="12" r="9"/><ellipse cx="12" cy="12" rx="4" ry="9"/><line x1="3" y1="12" x2="21" y2="12"/></g></svg></li>
        <li><span>512 Parmley Rd (Cnr Parmley Rd &amp; Osgood Creek Drive)<br>Tindarra Court Shopping Centre, Ashvale, SA 5199</span>
          <svg viewBox="0 0 24 24"><path fill="var(--ink)" d="M12 2a7 7 0 0 0-7 7c0 5 7 13 7 13s7-8 7-13a7 7 0 0 0-7-7zm0 9.5A2.5 2.5 0 1 1 12 6.5a2.5 2.5 0 0 1 0 5z"/></svg></li>
      </ul>
    </div>
  </section>

</body>
</html>
```